Mobile Fitness snd Therapy Business Card Design

I need a business card designed for my mobile fitness and therapy business.

Please view the images that I have uploaded. I like the simplicity of the design that I have attached. I adapted it with my information

Target Market(s)

Those seeking personal training, injury rehabilitation or massage therapy.

Industry/Entity Type

Business

Contact Information for Business Card

Derek Fulham - MSc, CAT(C), RMT, CSCS, Pn2
e-mail: derek@vantrelo.com
website: www.vantrelo.com
instagram: @derek_fulham

Font styles to use
Sans Serif

Colors
3176b5
0355a3

Requirements
Must have
• "Contact us to receive a FREE assessment"
• Services offered:
• Personal Training
• Golf Fitness
• Injury Rehab
• Massage Therapy
• Yoga
Nice to have
• Consistent colours with brand
• - Dark Blue: #232837
• - Blue: #5096f0
• Consistent look/feel with the website: www.vantrelo.com

```html
<!DOCTYPE html>
<html lang="en">
<head>
<meta charset="utf-8">
<title>Vantrelo Business Card</title>
<link href="https://fonts.googleapis.com/css2?family=Arimo:wght@400;700&display=swap" rel="stylesheet">
<style>
  :root {
    --navy: #232837;
    --blue: #5096f0;
    --blue-light: #8bbcf8;
    --blue-deep: #2a5bd6;
    --name-blue: #6aaaf5;
    --white: #ffffff;
    --stage: #eceef2;
  }
  * { margin: 0; padding: 0; box-sizing: border-box; }
  html, body {
    width: 1200px; height: 900px; overflow: hidden;
    background: var(--stage);
    font-family: "Arimo", Arial, sans-serif;
  }
  .canvas { position: relative; width: 1200px; height: 900px; }

  .card {
    position: absolute;
    border-radius: 14px;
    overflow: hidden;
    background: var(--white);
    box-shadow: 0 10px 30px rgba(35, 40, 55, 0.18);
  }
  .card-front { left: 178px; top: 73px; width: 588px; height: 365px; }
  .card-back  { left: 388px; top: 505px; width: 567px; height: 352px; }

  .front-shapes { position: absolute; inset: 0; }

  .wordmark {
    position: absolute; left: 0; right: 0; top: 62px;
    text-align: center;
    font-weight: 700; font-size: 46px; letter-spacing: 5px;
    color: var(--navy);
  }
  .tagline {
    position: absolute; left: 0; right: 0; top: 117px;
    text-align: center;
    font-weight: 700; font-size: 15px; letter-spacing: 2.4px;
    color: var(--navy);
  }

  .services {
    position: absolute; left: 25px; top: 242px;
    list-style: none;
    color: var(--white); font-size: 15px; line-height: 20px;
  }
  .services li { position: relative; padding-left: 12px; }
  .services li::before {
    content: ""; position: absolute; left: 0; top: 6px;
    width: 8px; height: 8px; border-radius: 50%;
    background: var(--blue-light);
  }

  .contact {
    position: absolute; right: 21px; top: 214px;
    text-align: right;
  }
  .contact .name {
    font-weight: 700; font-size: 19px; color: var(--name-blue);
    line-height: 24px;
  }
  .contact .credentials {
    font-size: 14.5px; color: var(--blue); line-height: 24px;
  }
  .contact .lines { margin-top: 10px; list-style: none; }
  .contact .lines li {
    display: flex; justify-content: flex-end; align-items: center; gap: 5px;
    color: var(--white); font-size: 14.5px; line-height: 22.5px;
  }
  .contact .icon { width: 12px; height: 12px; flex: none; }

  .back-panel {
    position: absolute; left: 262px; top: 0; right: 0; bottom: 0;
    background: var(--navy);
  }
  .offer {
    position: absolute; left: 325px; top: 93px;
    font-weight: 700; font-size: 25px; line-height: 45px;
    color: var(--blue); text-transform: uppercase;
  }
</style>
</head>
<body>
<main class="canvas">

  <section class="card card-front" aria-label="Business card front">
    <svg class="front-shapes" width="588" height="365" viewBox="0 0 588 365" aria-hidden="true">
      <path d="M0 207 H372 L386 190 L380 172 H588 V365 H0 Z" fill="var(--navy)"/>
      <rect x="0" y="182" width="117" height="18" rx="6" fill="var(--blue-light)"/>
      <rect x="125" y="182" width="117" height="18" rx="6" fill="var(--blue)"/>
      <rect x="251" y="182" width="118" height="18" rx="6" fill="var(--blue-deep)"/>
    </svg>

    <div class="wordmark">VANTRELO</div>
    <div class="tagline">NUTRITION - FITNESS - HEALTH</div>

    <ul class="services">
      <li>Personal Training</li>
      <li>Golf Fitness</li>
      <li>Injury Rehab</li>
      <li>Massage Therapy</li>
      <li>Yoga</li>
    </ul>

    <div class="contact">
      <div class="name">DEREK FULHAM</div>
      <div class="credentials">MSc, CAT(C), RMT, CSCS, Pn2</div>
      <ul class="lines">
        <li>derek@vantrelo.com
          <svg class="icon" viewBox="0 0 12 12" aria-hidden="true">
            <rect x="0" y="2" width="12" height="8" rx="1" fill="var(--blue)"/>
            <path d="M0.5 2.5 L6 6.5 L11.5 2.5" fill="none" stroke="var(--navy)" stroke-width="1"/>
          </svg>
        </li>
        <li>www.vantrelo.com
          <svg class="icon" viewBox="0 0 12 12" aria-hidden="true">
            <circle cx="6" cy="6" r="5.5" fill="var(--blue)"/>
            <ellipse cx="6" cy="6" rx="2.3" ry="5.5" fill="none" stroke="var(--navy)" stroke-width="0.9"/>
            <line x1="0.5" y1="6" x2="11.5" y2="6" stroke="var(--navy)" stroke-width="0.9"/>
          </svg>
        </li>
        <li>@derek_fulham
          <svg class="icon" viewBox="0 0 12 12" aria-hidden="true">
            <rect x="0" y="0" width="12" height="12" rx="2" fill="var(--blue)"/>
          </svg>
        </li>
      </ul>
    </div>
  </section>

  <section class="card card-back" aria-label="Business card back">
    <div class="back-panel"></div>
    <p class="offer">Contact us to<br>receive<br>a free<br>assessment</p>
  </section>

</main>
</body>
</html>
```